Glass Fabricator Presentation Folders

We need a folder to hold information about our company. We fabricate, laminate, temper, and digitally print any design on glass. All of this is done under one roof in our 80,000 square foot facility. Our digital printing is done by Vorn Lume technology, and is the first digital printer in the Southeastern United States. Our customers consist of commercial glaziers, architects, and designers. I have attached our existing logo.

Industry/Entity Type

It Company

Contact Information for Business Card

Harlow Pane Works, LLC
2380NW 42nd Avenue
Pompano Beach, Florida 33069
Phone: 954-615-3871
Fax:954-615-3902
www.harlowpane.example

```html
<!DOCTYPE html>
<html lang="en">
<head>
<meta charset="utf-8">
<title>Harlow Pane Works, LLC — Business Card</title>
<link rel="stylesheet" href="https://fonts.googleapis.com/css2?family=Lato:wght@400;700;900&display=swap">
<style>
  :root {
    --backdrop: #e6e2dc;
    --card-black: #070707;
    --card-white: #ffffff;
    --card-grey: #e2e2e2;
    --ink: #0a0a0a;
    --ink-soft: #d2d2d2;
    --paper-edge: #d3d3d3;
  }
  * { box-sizing: border-box; margin: 0; padding: 0; }
  html, body {
    width: 1200px;
    height: 900px;
    overflow: hidden;
    background: var(--backdrop);
    font-family: "Lato", Arial, sans-serif;
  }
  .canvas {
    position: relative;
    width: 1200px;
    height: 900px;
  }
  .card {
    position: absolute;
    width: 580px;
    height: 340px;
    overflow: hidden;
    box-shadow: 0 4px 0 var(--paper-edge), 0 16px 32px rgba(0,0,0,0.22);
  }

  /* Back of card */
  .card-back {
    left: 60px;
    top: 110px;
    background: var(--card-black);
    display: flex;
    align-items: center;
    justify-content: center;
    gap: 20px;
  }
  .card-back .brand-square {
    width: 40px;
    height: 40px;
    background: var(--card-white);
  }
  .card-back .brand-name {
    color: var(--card-white);
    font-weight: 900;
    font-size: 34px;
    letter-spacing: 1px;
    text-transform: uppercase;
    line-height: 1.05;
  }

  /* Front of card */
  .card-front {
    left: 560px;
    top: 455px;
    background: var(--card-black);
  }
  .card-front .brand-band {
    height: 155px;
    background: linear-gradient(160deg, var(--card-white) 30%, var(--card-grey) 100%);
    display: flex;
    align-items: center;
    justify-content: center;
    gap: 14px;
  }
  .card-front .brand-square {
    width: 30px;
    height: 30px;
    background: var(--ink);
  }
  .card-front .brand-name {
    color: var(--ink);
    font-weight: 900;
    font-size: 30px;
    letter-spacing: 1px;
    text-transform: uppercase;
  }
  .details {
    display: flex;
    height: 185px;
    padding: 24px 24px 0 24px;
    color: var(--card-white);
  }
  .person {
    width: 276px;
    text-align: right;
    padding-right: 22px;
  }
  .person .name { font-size: 24px; font-weight: 400; line-height: 1.2; }
  .person .role { font-size: 17px; color: var(--ink-soft); margin-bottom: 14px; }
  .person .address { font-size: 19px; line-height: 1.35; }
  .contact-list { list-style: none; }
  .contact-list li {
    display: flex;
    align-items: center;
    gap: 8px;
    font-size: 16px;
    line-height: 1;
    margin-bottom: 9px;
  }
  .contact-icon {
    width: 17px;
    height: 17px;
    flex: none;
  }
</style>
</head>
<body>
<main class="canvas">

  <section class="card card-back" aria-label="Business card, back">
    <span class="brand-square" aria-hidden="true"></span>
    <span class="brand-name">Harlow Pane<br>Works, LLC</span>
  </section>

  <section class="card card-front" aria-label="Business card, front">
    <header class="brand-band">
      <span class="brand-square" aria-hidden="true"></span>
      <span class="brand-name">Harlow Pane Works, LLC</span>
    </header>

    <div class="details">
      <div class="person">
        <p class="name">John Smith</p>
        <p class="role">Managing Director</p>
        <p class="address">1234, Address GoesHere<br>Country, 12345</p>
      </div>

      <ul class="contact-list">
        <li>
          <svg class="contact-icon" viewBox="0 0 16 16" aria-hidden="true">
            <rect width="16" height="16" rx="3" fill="#fff"/>
            <path d="M4 5.5c0-1 1-1.8 4-1.8s4 .8 4 1.8v1h-2.2V5.4H6.2v1.1H4z M5 8h6l1 4H4z" fill="#000"/>
          </svg>
          <span>123-456-7890</span>
        </li>
        <li>
          <svg class="contact-icon" viewBox="0 0 16 16" aria-hidden="true">
            <rect width="16" height="16" rx="3" fill="#fff"/>
            <rect x="4" y="3" width="8" height="4" fill="none" stroke="#000" stroke-width="1.2"/>
            <rect x="3" y="7" width="10" height="6" fill="#000"/>
            <rect x="5" y="9" width="6" height="1" fill="#fff"/>
          </svg>
          <span>123-456-7890</span>
        </li>
        <li>
          <svg class="contact-icon" viewBox="0 0 16 16" aria-hidden="true">
            <rect width="16" height="16" rx="3" fill="#fff"/>
            <rect x="3" y="4.5" width="10" height="7" fill="#000"/>
            <path d="M3 4.5l5 4 5-4" fill="none" stroke="#fff" stroke-width="1"/>
          </svg>
          <span>info@youremail.com</span>
        </li>
        <li>
          <svg class="contact-icon" viewBox="0 0 16 16" aria-hidden="true">
            <rect width="16" height="16" rx="3" fill="#fff"/>
            <path d="M7 9l2-2 M6.5 7.5l-1.5 1.5a1.6 1.6 0 0 0 2.3 2.3l1.5-1.5 M9.5 8.5l1.5-1.5a1.6 1.6 0 0 0-2.3-2.3L7.2 6.2" fill="none" stroke="#000" stroke-width="1.3" stroke-linecap="round"/>
          </svg>
          <span>www.yourweb.com</span>
        </li>
      </ul>
    </div>
  </section>

</main>
</body>
</html>
```